Cutting Edge Property Services Provider is Looking to Update Business Card Design

We are looking to freshen up our business cards to match our cutting edge technology based image.

KORVANEX - Where Care Finds Its Pulse

More information about our company can be found on our website at www.korvanex-demo.net

We integrate technology in a historically low tech industry.

We have appeared on the Brisk 300/3000 list 2 years in a row and we're previously recognized as the 5th Quickest Rising Firm in San Diego.

Our core colors are blue and white, but are not against accents that might improve our image.

We currently have our Mission Statement on our Business Cards in a folding design:
KORVANEX IS THE LEADING BUILDING SERVICES INNOVATOR. BY COMBINING TECHNOLOGY WITH FUNCTIONAL TOOS THAT IMPROVE EFFICIENCY IN THE WORKPLACE, WE PROVIDE UNPARALLELED SERVICE IN THE INDUSTRY. DEVELOPING LASTING RELATIONSHIPS WITH OUR CLIENTS AND ASSOCIATES IS THE CORNERSTONE OF OUR SUCCESS.

We'd like to convey the image of a cutting edge, technology based company. Want the cards to pop.

Target Market(s)

Commercial Property Managers - 20 to 50 year old professionals

Industry/Entity Type

Business

Requirements
Must have
• Must utilize our logo obviously, but are definitely open to using variations on the logo. Utilizing the components of the logo, but maybe in different configurations or backgrounds, etc...

Must use the Name: KORVANEX.
Can also use KORVANEX PROPERTY SERVICES.

Must include the Mission Statement

Must say: Where Care Finds Its Pulse
Nice to have
• We are considering plastic stock, shaped cards, or folding cards.

Nothing over the top or really expensive, but will consider if it conveys innovation and technology.
Should not have
• No images of toilets, buildings, trees, or anything relating to commercial properties.

We want to convey our technology image.

```html
<!DOCTYPE html>
<html lang="en">
<head>
<meta charset="utf-8">
<title>KORVANEX Folding Business Card</title>
<link rel="stylesheet" href="https://fonts.googleapis.com/css2?family=Open+Sans:wght@400;600;700&display=swap">
<style>
  :root {
    --board: #141414;
    --board-light: #2a2a2a;
    --label-red: #e4202a;
    --brand-blue: #0b4a7c;
    --card-white: #ffffff;
    --ink: #222222;
    --muted: #555555;
    --pattern-tint: #dfe6ee;
  }
  * { box-sizing: border-box; margin: 0; padding: 0; }
  html, body { width: 1200px; height: 810px; overflow: hidden; }
  body {
    position: relative;
    background: linear-gradient(90deg, var(--board), var(--board-light) 30%, var(--board) 55%, var(--board-light) 80%, var(--board));
    font-family: "Open Sans", Arial, sans-serif;
  }
  .panel-label {
    position: absolute;
    width: 543px;
    text-align: center;
    color: var(--label-red);
    font-weight: 700;
    font-size: 34px;
    letter-spacing: 5px;
  }
  .label-inner-top { left: 52px; top: 20px; }
  .label-front { left: 623px; top: 20px; }
  .label-inner-bottom { left: 52px; top: 728px; }
  .label-back { left: 623px; top: 728px; }

  .card {
    position: absolute;
    width: 543px;
    height: 309px;
    background: var(--card-white);
    border-radius: 26px;
    overflow: hidden;
  }
  .card-inner-top { left: 52px; top: 80px; }
  .card-front { left: 623px; top: 80px; }
  .card-inner-bottom { left: 52px; top: 407px; }
  .card-back { left: 623px; top: 407px; }

  .brand {
    position: absolute;
    left: 0; right: 0;
    display: flex;
    align-items: center;
    justify-content: center;
    gap: 14px;
    color: var(--brand-blue);
    font-weight: 700;
  }
  .brand-square { background: var(--brand-blue); flex: none; }

  .card-inner-top .brand { top: 95px; font-size: 52px; letter-spacing: 3px; }
  .card-inner-top .brand-square { width: 44px; height: 44px; }
  .card-inner-top .web {
    position: absolute; left: 0; right: 0; top: 262px;
    text-align: center; font-size: 19px; letter-spacing: 3px; color: var(--ink);
  }

  .card-front .brand { top: 52px; font-size: 36px; letter-spacing: 2px; }
  .card-front .brand-square { width: 32px; height: 32px; }
  .holder {
    position: absolute; right: 297px; top: 195px; text-align: right;
  }
  .holder-name { color: var(--brand-blue); font-size: 21px; line-height: 24px; }
  .holder-title { color: var(--muted); font-size: 13px; }
  .divider { position: absolute; left: 256px; top: 190px; width: 1px; height: 60px; background: #999; }
  .contacts { position: absolute; left: 266px; top: 184px; list-style: none; font-size: 14px; color: var(--ink); }
  .contacts li { display: flex; align-items: center; gap: 6px; height: 21px; }
  .contacts svg { width: 11px; height: 11px; fill: none; stroke: var(--ink); stroke-width: 1.6; }
  .address {
    position: absolute; left: 0; right: 0; top: 262px;
    text-align: center; font-size: 14.5px; color: var(--ink);
  }

  .faint-swirl {
    position: absolute; inset: 0;
    background: radial-gradient(ellipse 60% 55% at 50% 50%, var(--card-white) 30%, #eef2f6 55%, var(--card-white) 80%);
  }
  .mission {
    position: absolute; left: 0; right: 0; top: 62px;
    text-align: center; color: var(--brand-blue);
    font-size: 15.5px; line-height: 30px;
  }

  .pattern-field {
    position: absolute; inset: 0;
    background: linear-gradient(135deg, #f3f6f9, var(--pattern-tint) 50%, #f3f6f9);
  }
  .card-back .brand { top: 118px; font-size: 56px; letter-spacing: 4px; }
  .card-back .brand-square { width: 46px; height: 46px; }
  .tagline {
    position: absolute; left: 0; right: 0; top: 248px;
    text-align: center; color: var(--brand-blue);
    font-weight: 700; font-size: 23px;
  }
</style>
</head>
<body>
  <div class="panel-label label-inner-top">Inner Top</div>
  <div class="panel-label label-front">Front</div>
  <div class="panel-label label-inner-bottom">Inner Bottom</div>
  <div class="panel-label label-back">Back</div>

  <section class="card card-inner-top">
    <div class="brand"><span class="brand-square"></span>KORVANEX</div>
    <p class="web">www.korvanex-demo.net</p>
  </section>

  <section class="card card-front">
    <div class="brand"><span class="brand-square"></span>KORVANEX</div>
    <div class="holder">
      <div class="holder-name">Your Name</div>
      <div class="holder-title">Title</div>
    </div>
    <div class="divider"></div>
    <ul class="contacts">
      <li><svg viewBox="0 0 12 12"><path d="M2 1.5l2.5 0 1 2.5-1.5 1a6 6 0 0 0 3 3l1-1.5 2.5 1v2.5c-5 .5-9-3.5-8.5-8.5z"/></svg>1(866) 555-0142</li>
      <li><svg viewBox="0 0 12 12"><rect x="1" y="2.5" width="10" height="7"/><path d="M1 2.5l5 4 5-4"/></svg>info@korvanex-demo.net</li>
      <li><svg viewBox="0 0 12 12"><circle cx="6" cy="6" r="5"/><path d="M1 6h10M6 1c-3 3-3 7 0 10M6 1c3 3 3 7 0 10"/></svg>www.korvanex-demo.net</li>
    </ul>
    <p class="address">2150 Harbor Ridge Blvd., Suite 210, Lakemont, OR 97031</p>
  </section>

  <section class="card card-inner-bottom">
    <div class="faint-swirl" role="img" aria-label="Faint large brand swirl watermark"></div>
    <p class="mission">
      Korvanex is The Leading Building Services Innovator.<br>
      By Combining Technology With Functional Toos That<br>
      Improve Efficiency In The Workplace, We Provide<br>
      Unparalleled Service in The Industry. Developing<br>
      Lasting Relationships With Our Clients and Associates<br>
      is The Cornerstone of Our Success.
    </p>
  </section>

  <section class="card card-back">
    <div class="pattern-field" role="img" aria-label="Repeating pale blue brand swirl pattern"></div>
    <div class="brand"><span class="brand-square"></span>KORVANEX</div>
    <p class="tagline">Where Care Finds Its Pulse</p>
  </section>
</body>
</html>
```